Business Card for a mobile physiotherapy company

I need a layout for a business card for a mobile physiotherapy company.
Slogan is "Mobile Physiotherapy - Your Road To Recovery"
Phone number is 867-555-0142
Email VardenTherapy@postnest.ca (subject to change with website)
Website www.VardenTherapy.ca
My name and credentials: Luke Varden Luke Varden, BSc(kin), MPT, CAFCI, IMS
Information maybe included: Direct Billing, Services including Physiotherapy, IMS, acupuncture
Maybe include facebook and instagram logos
One side with the logo clean and sharp
Other side with details, try not to look too busy, keep everything concise

```html
<!DOCTYPE html>
<html lang="en">
<head>
<meta charset="utf-8">
<title>Varden Therapy – Business Card</title>
<link rel="stylesheet" href="https://fonts.googleapis.com/css2?family=Arimo:wght@400;700&display=swap">
<style>
  :root {
    --backdrop: #2a2a2a;
    --teal: #0d5a4f;
    --teal-dark: #0a4a41;
    --navy: #203a6b;
    --paper: #f7f7f7;
    --ink: #1d1d1d;
    --muted: #555;
    --on-teal: #f2f2f2;
  }
  * { box-sizing: border-box; margin: 0; padding: 0; }
  html, body { width: 1200px; height: 997px; overflow: hidden; }
  body {
    background: var(--backdrop);
    font-family: "Arimo", Arial, sans-serif;
    position: relative;
  }
  .card {
    position: absolute;
    width: 560px;
    height: 320px;
    border-radius: 0 46px 0 46px;
    box-shadow: 0 14px 30px rgba(0,0,0,.45);
  }

  /* Logo side */
  .card--logo {
    left: 60px; top: 110px;
    background: var(--teal);
    color: var(--on-teal);
    display: flex; flex-direction: column; align-items: center; justify-content: center;
    text-align: center;
  }
  .card--logo .brand {
    display: flex; align-items: center; gap: 14px;
    font-size: 44px; font-weight: 700; letter-spacing: 4px;
  }
  .card--logo .brand-mark {
    width: 22px; height: 22px; background: var(--on-teal);
  }
  .card--logo .offer-label {
    margin-top: 38px; font-size: 12px; letter-spacing: 1.5px; opacity: .85;
  }
  .card--logo .offer-list {
    margin-top: 6px; font-size: 13px; letter-spacing: 1px;
  }

  /* Details side */
  .card--details {
    left: 580px; top: 500px;
    background: var(--paper);
    color: var(--ink);
  }
  .card--details .brand {
    position: absolute; left: 34px; top: 120px; width: 230px;
    display: flex; align-items: center; gap: 10px;
    color: var(--teal);
    font-size: 25px; font-weight: 700; letter-spacing: 2px;
  }
  .card--details .brand-mark {
    width: 14px; height: 14px; background: var(--teal); flex: none;
  }
  .divider {
    position: absolute; left: 278px; top: 46px;
    width: 1px; height: 140px; background: var(--teal);
  }
  .contact {
    position: absolute; left: 300px; top: 46px;
  }
  .contact .name {
    color: var(--teal); font-weight: 700; font-size: 14px; letter-spacing: .5px;
  }
  .contact .credentials { font-size: 11px; color: var(--muted); margin-top: 2px; }
  .contact ul { list-style: none; margin-top: 16px; }
  .contact li {
    display: flex; align-items: center; gap: 8px;
    font-size: 12px; line-height: 19px;
  }
  .contact li.web { font-weight: 700; }
  .contact svg { width: 11px; height: 11px; fill: var(--ink); flex: none; }
  .contact .dot { width: 9px; height: 9px; border-radius: 50%; background: var(--ink); margin: 0 1px; flex: none; }
  .slogan {
    position: absolute; left: 0; right: 0; bottom: 52px;
    text-align: center; color: var(--teal);
    font-weight: 700; font-size: 14px; letter-spacing: .3px;
  }
</style>
</head>
<body>

<section class="card card--logo">
  <div class="brand"><span class="brand-mark"></span>VARDEN THERAPY</div>
  <p class="offer-label">WE OFFER</p>
  <p class="offer-list">DIRECT BILLING, PHYSIOTHERAPY, IMS, ACUPUNCTURE</p>
</section>

<section class="card card--details">
  <div class="brand"><span class="brand-mark"></span>VARDEN THERAPY</div>
  <div class="divider"></div>
  <div class="contact">
    <p class="name">LUKE VARDEN</p>
    <p class="credentials">BSc(kin), MPT, CAFCI, IMS</p>
    <ul>
      <li><svg viewBox="0 0 24 24"><path d="M6.6 10.8a15.2 15.2 0 0 0 6.6 6.6l2.2-2.2c.3-.3.7-.4 1-.2 1.1.4 2.3.6 3.6.6.6 0 1 .4 1 1V20c0 .6-.4 1-1 1A17 17 0 0 1 3 4c0-.6.4-1 1-1h3.5c.6 0 1 .4 1 1 0 1.3.2 2.5.6 3.6.1.3 0 .7-.2 1z"/></svg>867-555-0142</li>
      <li><svg viewBox="0 0 24 24"><path d="M2 5h20v14H2zm2 2v.5l8 5 8-5V7l-8 5z"/></svg>VardenTherapy@postnest.ca</li>
      <li><span class="dot"></span>VardenTherapy</li>
      <li><span class="dot"></span>VardenTherapy</li>
      <li class="web"><svg viewBox="0 0 24 24"><path d="M12 2a10 10 0 1 0 0 20 10 10 0 0 0 0-20zm0 2c1 1.3 1.8 3 2.2 5H9.8C10.2 7 11 5.3 12 4zM4.3 13a8 8 0 0 1 0-2h3.3a16 16 0 0 0 0 2zm5.5 2h4.4c-.4 2-1.2 3.7-2.2 5-1-1.3-1.8-3-2.2-5zm-.2-2a14 14 0 0 1 0-2h4.8a14 14 0 0 1 0 2zm6.8 0a16 16 0 0 0 0-2h3.3a8 8 0 0 1 0 2z"/></svg>www.VardenTherapy.ca</li>
    </ul>
  </div>
  <p class="slogan">Mobile Physiotherapy - Your Road To Recovery</p>
</section>

</body>
</html>
```